We are a doctors medical practice
I need the business card to be eye catching and memorable,
to reflect professionalism, yet also warmth and care

the numbers need to be easy to see, for the elderly

and the logo also in a location that is large enough to see and be eye catching

Back of card:
opening hours:
Mon- Fri 8.30am to 6pm
Sat 9am to 4pm

rows for appontments, date and time
Updates

HiĀ 

Modification to company name

BROOKVALE KINDRED HEALTH MEDICAL PRACTICE

Thanks
Marla

Reason: I am look for a unique design that also fulfils the design brief

I have attempted to post a .eps and .ai file of the logo

Target Market(s)

needs to appeal to the majority, mainly adults

Industry/Entity Type

Medical

Contact Information for Business Card

company name: Brookvale Kindred Health Medical Practice
Name: Dr Marla Tobrik-Vey
Qualifications: MBBS, Bsci(med), FRACGP, DCH, SH&FPA, Dip Derm
Address: Shop 3/41-43 Corrow St, Fairfield 2165
Ph: 02 9184 3025
Fax: 02 9318 6042

Requirements
Nice to have
• I like balance
gold/ silver incorporated, as well as the other colours in the logo- but not limited to these colours
a "medical" feel
Should not have
• dark or strong colours

```html
<!DOCTYPE html>
<html lang="en">
<head>
<meta charset="utf-8">
<title>Brookvale Kindred Health Medical Practice – Business Card</title>
<link rel="stylesheet" href="https://fonts.googleapis.com/css2?family=Open+Sans:wght@400;600;700;800&display=swap">
<style>
  :root {
    --page-bg: #ffffff;
    --card-blue-light: #2f86e0;
    --card-blue-mid: #1766c9;
    --card-blue-deep: #0b47a3;
    --band-blue: rgba(6, 40, 110, 0.55);
    --accent-gold: #f6c21c;
    --text-white: #ffffff;
    --caption-ink: #111111;
    --field-white: #ffffff;
    --logo-disc: #e9f3fc;
  }
  * { box-sizing: border-box; margin: 0; padding: 0; }
  html, body {
    width: 900px; height: 1200px; overflow: hidden;
    background: var(--page-bg);
    font-family: "Open Sans", Arial, sans-serif;
  }
  .sheet { position: relative; width: 900px; height: 1200px; }

  .card {
    position: absolute; left: 70px; width: 760px; height: 434px;
    overflow: hidden; color: var(--text-white);
  }
  .card--front { top: 50px; }
  .card--back { top: 600px; }
  .card__surface {
    position: absolute; inset: 0;
    background: radial-gradient(ellipse at 40% 35%, var(--card-blue-light) 0%, var(--card-blue-mid) 45%, var(--card-blue-deep) 100%);
  }
  .caption {
    position: absolute; left: 0; width: 900px; text-align: center;
    font-weight: 700; font-size: 22px; color: var(--caption-ink);
  }
  .caption--front { top: 500px; }
  .caption--back { top: 1050px; }

  /* Front */
  .doctor {
    position: absolute; right: 34px; top: 24px; text-align: right;
  }
  .doctor__name { font-size: 27px; font-weight: 700; }
  .doctor__quals { font-size: 15px; font-weight: 600; color: var(--accent-gold); line-height: 1.35; margin-top: 4px; }

  .name-band {
    position: absolute; left: 0; right: 0; top: 146px; height: 100px;
    background: var(--band-blue);
  }
  .brand {
    position: absolute; display: flex; align-items: center; gap: 22px;
  }
  .brand--front { left: 28px; top: 126px; }
  .brand__disc {
    width: 140px; height: 140px; border-radius: 50%;
    background: var(--logo-disc); flex: none;
  }
  .brand__name {
    font-size: 33px; font-weight: 800; line-height: 1.12; color: var(--text-white);
    text-transform: uppercase;
  }

  .contact {
    position: absolute; left: 44px; top: 282px; list-style: none;
    font-size: 20px; font-weight: 600; line-height: 1.3;
  }
  .contact li { display: flex; align-items: center; gap: 16px; min-height: 36px; }
  .contact__address { margin-bottom: 8px; }
  .contact svg { width: 22px; height: 22px; flex: none; }

  .hours {
    position: absolute; right: 34px; top: 288px; text-align: right;
    font-size: 19px; font-weight: 600; line-height: 1.4;
  }
  .hours__title { color: var(--accent-gold); font-size: 23px; font-weight: 700; }

  /* Back */
  .brand--back {
    left: 0; right: 0; top: 22px; flex-direction: column; gap: 10px;
  }
  .brand--back .brand__disc { width: 130px; height: 130px; }
  .brand--back .brand__name { font-size: 31px; text-align: center; }

  .appointment { position: absolute; left: 30px; right: 30px; top: 232px; font-size: 19px; font-weight: 600; }
  .appointment__row { display: flex; align-items: center; gap: 12px; height: 34px; margin-bottom: 18px; }
  .field { background: var(--field-white); height: 32px; }
  .field--next { flex: 1; margin-left: 8px; }
  .field--day { width: 190px; }
  .field--date { width: 170px; }
  .field--time { flex: 1; }
  .appointment__label--gap { margin-left: 10px; }

  .hours-band {
    position: absolute; left: 0; right: 0; bottom: 34px; height: 46px;
    background: var(--band-blue); display: flex; align-items: center; justify-content: center;
    font-size: 19px; font-weight: 600;
  }
</style>
</head>
<body>
<main class="sheet">

  <section class="card card--front" aria-label="Business card front">
    <div class="card__surface" role="img" aria-label="Blue gradient background with soft diamond pattern"></div>
    <div class="name-band"></div>
    <div class="doctor">
      <p class="doctor__name">Dr Marla Tobrik-Vey</p>
      <p class="doctor__quals">MBBS, Bsci(med), FRACGP, DCH,<br>SH&amp;FPA, Dip Derm</p>
    </div>
    <div class="brand brand--front">
      <div class="brand__disc"></div>
      <p class="brand__name">Brookvale Kindred Health<br>Medical</p>
    </div>
    <ul class="contact">
      <li class="contact__address">
        <svg viewBox="0 0 24 24" aria-hidden="true"><path fill="#f6c21c" d="M12 2a7 7 0 0 0-7 7c0 5 7 13 7 13s7-8 7-13a7 7 0 0 0-7-7zm0 9.5A2.5 2.5 0 1 1 12 6.5a2.5 2.5 0 0 1 0 5z"/></svg>
        <span>Shop 3/41-43 Corrow St,<br>Dunmore Vale 2371</span>
      </li>
      <li>
        <svg viewBox="0 0 24 24" aria-hidden="true"><path fill="#f6c21c" d="M6.6 10.8a15 15 0 0 0 6.6 6.6l2.2-2.2a1 1 0 0 1 1-.25 11.4 11.4 0 0 0 3.6.57 1 1 0 0 1 1 1V20a1 1 0 0 1-1 1A17 17 0 0 1 3 4a1 1 0 0 1 1-1h3.5a1 1 0 0 1 1 1c0 1.25.2 2.45.57 3.57a1 1 0 0 1-.25 1z"/></svg>
        <span>(02) 9184 3025</span>
      </li>
      <li>
        <svg viewBox="0 0 24 24" aria-hidden="true"><path fill="#f6c21c" d="M7 3h10v5H7zM4 9h16a2 2 0 0 1 2 2v6h-4v4H6v-4H2v-6a2 2 0 0 1 2-2zm4 7v3h8v-3z"/></svg>
        <span>(02) 9318 6042</span>
      </li>
    </ul>
    <div class="hours">
      <p class="hours__title">Opening Hours:</p>
      <p>Mon- Fri 8.30am to 6pm</p>
      <p>Sat 9am to 4pm</p>
    </div>
  </section>
  <p class="caption caption--front">Front Design with your suggested changes.</p>

  <section class="card card--back" aria-label="Business card back">
    <div class="card__surface" role="img" aria-label="Blue gradient background with soft diamond pattern"></div>
    <div class="brand brand--back">
      <div class="brand__disc"></div>
      <p class="brand__name">Brookvale Kindred Health Medical</p>
    </div>
    <div class="appointment">
      <div class="appointment__row">
        <span>Your Next Appointment</span><span class="field field--next"></span>
      </div>
      <div class="appointment__row">
        <span>Day</span><span class="field field--day"></span>
        <span class="appointment__label--gap">Date</span><span class="field field--date"></span>
        <span class="appointment__label--gap">Time</span><span class="field field--time"></span>
      </div>
    </div>
    <div class="hours-band">Opening Hours: Mon- Fri 8.30am to 6pm | Sat 9am to 4pm</div>
  </section>
  <p class="caption caption--back">Back Design with your suggested changes.</p>

</main>
</body>
</html>
```